Lumora Systems New Website - IT Infrastructure | Smart Cabinet | Micro Data Center

We're an IT SI providing Server Room Design & Build | All-in-One Rack & Smart Cabinet | Structured Cabling | IT Relocation | Maintenance. Old website can be found at www.lumorasys.com.hk. We'd like a brand new wix website which is modern, minimalist, interactive with some animation. Website content will be mostly static and include our service, our project, news and events, about us, contacts, blogs, partners and brands, etc.

reference sites:
We'd like to see more designs referring to below

https://www.pixelvane.example/design/41736205
https://www.pixelvane.example/design/41892417
https://velbrinn.example/

Animation (scrolling effect) referring to
https://velbrinn.example/intelligence/smart-office-room/
Updates

we'd like below style.

Designs look the same

Target Market(s)

Commercials in HK

Industry/Entity Type

IT, Technology, Data Center

Coding

Coded - Design and coding required

Font styles to use
Sans Serif

Requirements
Must have
• CMS, Some Interactive Elements/ Graphics

```html
<!DOCTYPE html>
<html lang="en">
<head>
<meta charset="utf-8">
<title>Lumora Systems – IT Infrastructure</title>
<link href="https://fonts.googleapis.com/css2?family=Roboto:wght@400;500;700&family=Russo+One&display=swap" rel="stylesheet">
<style>
:root{
  --red:#d1321f;
  --red-dark:#b82a19;
  --navy:#141a33;
  --ink:#222633;
  --muted:#6b6f7a;
  --light:#eeeff1;
  --white:#ffffff;
}
*{box-sizing:border-box;margin:0;padding:0}
html,body{width:1200px;height:3853px;overflow:hidden}
body{position:relative;font-family:"Roboto",sans-serif;color:var(--ink);background:var(--white)}
.abs{position:absolute}
.display{font-family:"Russo One",sans-serif;font-weight:400}
.section-title{position:absolute;left:0;width:1200px;text-align:center;font-size:40px;color:var(--navy)}
.section-title::after{content:"";display:block;width:78px;height:4px;background:var(--red);margin:12px auto 0}
.btn{position:absolute;display:flex;align-items:center;justify-content:center;gap:8px;border-radius:24px;font-weight:700;font-size:14px;color:var(--white);background:var(--red);box-shadow:0 6px 14px rgba(209,50,31,.25)}
.arrow-dot{width:13px;height:13px;border-radius:50%;background:currentColor;position:relative}
.arrow-dot::after{content:"";position:absolute;left:3px;top:3.5px;border-left:6px solid var(--red);border-top:3px solid transparent;border-bottom:3px solid transparent}

/* header */
.site-header{position:absolute;left:0;top:0;width:1200px;height:73px;background:var(--white)}
.brand{position:absolute;display:flex;align-items:center;gap:8px;font-weight:500;color:var(--navy)}
.brand-mark{border:3px solid var(--red);border-radius:4px}
.nav{position:absolute;left:398px;top:28px;display:flex;gap:28px;font-size:14px;font-weight:500;color:var(--navy)}
.lang{position:absolute;left:768px;top:28px;font-size:14px;font-weight:500;display:flex;align-items:center;gap:6px}
.lang i{width:15px;height:15px;border-radius:50%;background:#c9cfe0;border:1px solid #9aa3bf}

/* hero */
.hero-photo{position:absolute;left:0;top:73px;width:1200px;height:540px;background:linear-gradient(100deg,#1f3047 0%,#2b4463 30%,#14202f 60%,#1b2535 100%)}
.hero-text{position:absolute;right:147px;top:174px;text-align:right;color:var(--white)}
.hero-text .kicker{font-size:15px;font-weight:700}
.hero-text h1{font-size:50px;margin-top:6px;line-height:1.1}
.hero-text p{font-size:15px;line-height:25px;margin-top:18px;font-weight:500}

/* about */
.about-copy{position:absolute;left:143px;top:816px;width:414px;font-size:13px;line-height:25px;color:var(--muted);text-align:justify}
.about-copy p+p{margin-top:12px}
.about-frame{position:absolute;left:748px;top:857px;width:323px;height:252px;border:3px solid var(--red);border-top:none;border-left:none}
.about-photo{position:absolute;left:621px;top:718px;width:432px;height:373px;background:linear-gradient(120deg,#2d4a4c,#7fa4a1 40%,#35524f 75%,#1c2c2e);box-shadow:0 8px 20px rgba(0,0,0,.15)}

/* services */
.services{position:absolute;left:0;top:1188px;width:1200px;height:589px;background:linear-gradient(180deg,#f1f2f4,#e6e7ea)}
.service-card{position:absolute;top:1322px;width:209px;height:383px;border-radius:105px;background:var(--white);border-top:12px solid var(--navy);border-bottom:12px solid var(--navy);text-align:center;padding-top:44px}
.service-card.featured{background:var(--red);color:var(--white)}
.service-icon{width:90px;height:90px;margin:0 auto;border-radius:50%;background:var(--navy);display:flex;align-items:center;justify-content:center}
.service-card h3{font-size:17px;font-weight:500;line-height:27px;margin-top:22px;padding:0 12px;color:var(--navy)}
.service-card p{font-size:12px;line-height:20px;color:var(--muted);margin-top:14px;padding:0 18px}
.service-card.featured h3,.service-card.featured p{color:var(--white)}
.service-card .more{position:absolute;left:0;right:0;bottom:40px;font-size:13px;font-weight:700;color:var(--navy);display:flex;justify-content:center;align-items:center;gap:7px}
.service-card .more .arrow-dot::after{border-left-color:var(--white)}
.service-card.featured .more{color:var(--white)}
.service-card.featured .more .arrow-dot::after{border-left-color:var(--red)}

/* projects */
.project-card{position:absolute;top:1951px;width:289px;height:314px;background:var(--white);box-shadow:0 4px 14px rgba(0,0,0,.08);text-align:center}
.project-img{height:191px;width:100%}
.project-card h3{font-size:15px;font-weight:500;line-height:23px;margin-top:16px;color:var(--navy)}
.project-card .loc{font-size:12px;color:var(--muted);margin-top:4px}
.project-card .read{font-size:12px;font-weight:700;color:var(--red);margin-top:8px;display:flex;justify-content:center;align-items:center;gap:6px}
.project-card .read .arrow-dot::after{border-left-color:var(--white)}
.chev{position:absolute;top:2026px;width:22px;height:22px;border-top:4px solid;border-right:4px solid}

/* partners */
.partner-tile{position:absolute;width:217px;height:101px;background:var(--white);box-shadow:0 4px 14px rgba(0,0,0,.07);display:flex;align-items:center;justify-content:center}
.badge{width:120px;height:30px;border-radius:6px;background:#cfd2d8}
.dots{position:absolute;left:578px;top:2726px;display:flex;gap:6px;align-items:center}
.dots i{width:7px;height:7px;border-radius:50%;background:#c4c6cc}
.dots i.on{width:14px;height:14px;border:2px solid var(--red);background:radial-gradient(var(--red) 40%,transparent 45%)}

/* contact */
.field{position:absolute;left:197px;width:391px;height:48px;border:1.5px solid rgba(255,255,255,.45);border-radius:24px;color:var(--white);font-size:12px;padding:16px 22px}
.field.message{left:609px;top:3053px;width:392px;height:240px;border-radius:24px}
.submit{position:absolute;left:519px;top:3335px;width:160px;height:42px;border-radius:21px;background:var(--white);color:var(--red);font-weight:700;font-size:14px;display:flex;align-items:center;justify-content:center}

/* footer */
.foot-col{position:absolute;top:3574px}
.foot-col h4{font-size:16px;font-weight:700;color:var(--navy);margin-bottom:12px}
.foot-col li{list-style:none;font-size:12.5px;color:var(--muted);line-height:30px;display:flex;gap:9px}
.foot-col li::before{content:"»";color:var(--red)}
.contact-list li{display:flex;gap:14px;line-height:21px;margin-bottom:11px}
.contact-list li::before{content:none}
.contact-list svg{flex:none;margin-top:3px}
.social{position:absolute;top:3707px;width:33px;height:33px;border-radius:50%;background:#e4e5e8}
.divider{position:absolute;left:143px;top:3789px;width:913px;height:1px;background:#dfe0e3}
.copyright{position:absolute;left:0;width:1200px;top:3811px;text-align:center;font-size:12px;color:var(--muted)}
.chat{position:absolute;left:1083px;top:3770px;width:36px;height:36px;border-radius:50%;background:var(--red);display:flex;align-items:center;justify-content:center}
</style>
</head>
<body>

<header class="site-header">
  <div class="brand" style="left:143px;top:18px;font-size:26px">
    <span class="brand-mark" style="width:30px;height:30px"></span>Lumora
  </div>
  <nav class="nav">
    <span style="color:var(--navy)">Home</span><span>About</span><span>Our Services</span><span>Our Projects</span>
  </nav>
  <div class="abs" style="left:412px;top:12px;width:11px;height:11px;border:2px solid var(--red);border-radius:2px"></div>
  <div class="lang"><i></i>Eng ▾</div>
  <svg class="abs" style="left:861px;top:29px" width="16" height="16" viewBox="0 0 16 16"><circle cx="6.5" cy="6.5" r="5" fill="none" stroke="#141a33" stroke-width="1.8"/><line x1="10" y1="10" x2="15" y2="15" stroke="#141a33" stroke-width="1.8"/></svg>
  <div class="btn" style="left:918px;top:15px;width:135px;height:41px;font-size:13px">CONTACT US</div>
</header>

<section class="hero">
  <div class="hero-photo" role="img" aria-label="Two engineers reviewing a laptop in a server room aisle"></div>
  <svg class="abs" style="left:0;top:500px" width="1200" height="150" viewBox="0 500 1200 150">
    <polygon points="0,613 650,613 770,534 1200,534 1200,650 0,650" fill="#fff"/>
    <polyline points="0,616 648,616 768,531 1200,531" fill="none" stroke="#141a33" stroke-width="5"/>
    <polygon points="0,624 655,624 788,512 1200,512 1200,522 795,522 662,636 0,636" fill="#d1321f"/>
  </svg>
  <div class="hero-text">
    <div class="kicker">Welcome To</div>
    <h1 class="display">Lumora Systems</h1>
    <p>Our dedication, focus, and expertise wins much recognition<br>of many IT professionals in all industries in the region.</p>
  </div>
  <div class="btn" style="left:869px;top:355px;width:184px;height:43px">GET STARTED <span class="arrow-dot"></span></div>
</section>

<section class="about">
  <h2 class="display abs" style="left:143px;top:722px;font-size:40px;color:var(--navy)">About Us</h2>
  <div class="abs" style="left:143px;top:776px;width:96px;height:4px;background:var(--red)"></div>
  <div class="about-copy">
    <p>Lumora Systems is well experienced in delivering the best in Data Center Infrastructure, Network Infrastructure, Structured Cabling, Telephony, Access Control, Video Surveillance, Audiovisual &amp; Conferencing, Relocation &amp; Migration and Maintenance solutions.</p>
    <p>Our dedication, focus, and expertise wins much recognition of many IT professionals in all industries in the region. In Lumora Systems' Belief, the major reason that we gain a lot of true.</p>
  </div>
  <div class="btn" style="left:143px;top:1034px;width:164px;height:42px">LEARN MORE <span class="arrow-dot"></span></div>
  <div class="about-frame"></div>
  <div class="about-photo" role="img" aria-label="Technician with a tablet checking racks in a data center"></div>
</section>

<section class="services">
  <h2 class="section-title display" style="top:52px">Our Services</h2>
</section>

<article class="service-card" style="left:132px">
  <div class="service-icon"><svg width="44" height="40" viewBox="0 0 44 40" fill="none" stroke="#fff" stroke-width="2"><rect x="8" y="3" width="28" height="8"/><rect x="8" y="13" width="28" height="8"/><path d="M12 36h22a6 6 0 0 0 0-12 8 8 0 0 0-15-1 6 6 0 0 0-7 13z" fill="#141a33"/></svg></div>
  <h3>Data center<br>design and build</h3>
  <p>All the components contained inside a Data Center are all critical...</p>
  <div class="more">LEARN MORE <span class="arrow-dot"></span></div>
</article>
<article class="service-card" style="left:374px">
  <div class="service-icon"><svg width="40" height="40" viewBox="0 0 40 40" fill="none" stroke="#fff" stroke-width="2.2"><path d="M14 4v8M24 4v8M9 12h20v8a10 10 0 0 1-20 0z"/><path d="M19 30v7"/><path d="M30 20l-4 7h5l-4 7" /></svg></div>
  <h3>Structured Cabling<br>and fiber backbone</h3>
  <p>From the walk through to cable design andinstallation, we ensure your entire..</p>
  <div class="more">LEARN MORE <span class="arrow-dot"></span></div>
</article>
<article class="service-card featured" style="left:616px">
  <div class="service-icon"><svg width="36" height="42" viewBox="0 0 36 42" fill="none" stroke="#fff" stroke-width="2"><rect x="5" y="3" width="26" height="36" rx="2"/><path d="M10 10h16M10 16h16M10 22h16M10 28h16"/></svg></div>
  <h3 style="margin-top:38px">All-In-One Rack<br>/ Micro-Data Center</h3>
  <p style="margin-top:2px">Our service provides highly skilled technical personnel, a sophisticated IT...</p>
  <div class="more">LEARN MORE <span class="arrow-dot"></span></div>
</article>
<article class="service-card" style="left:859px">
  <div class="service-icon"><svg width="44" height="40" viewBox="0 0 44 40" fill="none" stroke="#fff" stroke-width="2"><rect x="16" y="3" width="12" height="8"/><circle cx="10" cy="17" r="3"/><circle cx="34" cy="17" r="3"/><path d="M6 36v-10h8M38 36v-10h-8M14 26h16M22 26v10"/></svg></div>
  <h3>Audiovisual and<br>Conference Room</h3>
  <p>Heaps of office relocation, data center consolidation, business unit migration...</p>
  <div class="more">LEARN MORE <span class="arrow-dot"></span></div>
</article>

<section class="projects">
  <h2 class="section-title display" style="top:1850px">Our Projects</h2>
  <div class="chev" style="left:72px;border-color:#9a9da5;transform:rotate(-135deg)"></div>
  <div class="chev" style="left:1105px;border-color:var(--navy);transform:rotate(45deg)"></div>
  <article class="project-card" style="left:144px">
    <div class="project-img" role="img" aria-label="Open server racks with blue patch cabling" style="background:linear-gradient(180deg,#5a4d44,#2e2c2f 60%,#4a6a8a)"></div>
    <h3>A Renowned China based listed<br>insurance company</h3>
    <div class="loc">Location : Kowloon</div>
    <div class="read">READ MORE <span class="arrow-dot"></span></div>
  </article>
  <article class="project-card" style="left:456px">
    <div class="project-img" role="img" aria-label="Dense bundles of blue network cables in a rack" style="background:linear-gradient(90deg,#1d2f5a,#3b5ea8 50%,#1a2540 80%,#777)"></div>
    <h3>Harbourline International<br>&amp; Meridian</h3>
    <div class="loc">Location : Hong Kong</div>
    <div class="read">READ MORE <span class="arrow-dot"></span></div>
  </article>
  <article class="project-card" style="left:767px">
    <div class="project-img" role="img" aria-label="Smart cabinet micro data center in an office" style="background:linear-gradient(90deg,#cfcfcf,#3a3b3f 35%,#26272b 60%,#bdbdbd)"></div>
    <h3>A renowned China based<br>Securities firm</h3>
    <div class="loc">Location : Hong Kong</div>
    <div class="read">READ MORE <span class="arrow-dot"></span></div>
  </article>
</section>

<section class="partners">
  <h2 class="section-title display" style="top:2338px">Our Partners</h2>
  <div class="partner-tile" style="left:144px;top:2471px"><span class="badge"></span></div>
  <div class="partner-tile" style="left:376px;top:2471px"><span class="badge"></span></div>
  <div class="partner-tile" style="left:607px;top:2471px"><span class="badge"></span></div>
  <div class="partner-tile" style="left:839px;top:2471px"><span class="badge"></span></div>
  <div class="partner-tile" style="left:144px;top:2580px"><span class="badge"></span></div>
  <div class="partner-tile" style="left:376px;top:2580px"><span class="badge"></span></div>
  <div class="partner-tile" style="left:607px;top:2580px"><span class="badge"></span></div>
  <div class="partner-tile" style="left:839px;top:2580px"><span class="badge"></span></div>
  <div class="dots"><i class="on"></i><i></i><i></i></div>
</section>

<section class="contact">
  <svg class="abs" style="left:0;top:2810px" width="1200" height="710" viewBox="0 2810 1200 710">
    <defs><linearGradient id="redfill" x1="0" y1="0" x2="1" y2="1"><stop offset="0" stop-color="#c92d1b"/><stop offset=".6" stop-color="#d9442f"/><stop offset="1" stop-color="#c42a19"/></linearGradient></defs>
    <polygon points="0,2940 405,2940 540,2845 1200,2845 1200,3380 790,3380 668,3478 0,3478" fill="url(#redfill)"/>
    <polyline points="0,2950 400,2950 538,2832 1200,2832" fill="none" stroke="#141a33" stroke-width="12"/>
    <polyline points="0,3500 660,3500 783,3392 1200,3392" fill="none" stroke="#141a33" stroke-width="12"/>
  </svg>
  <h2 class="section-title display" style="top:2968px;color:var(--white)">Contact Us</h2>
  <style>.contact .section-title::after{background:var(--white)}</style>
  <div class="field" style="top:3056px">Name</div>
  <div class="field" style="top:3119px">Email Address</div>
  <div class="field" style="top:3182px">Phone Number</div>
  <div class="field" style="top:3245px">Company</div>
  <div class="field message">Message</div>
  <div class="submit">SUBMIT NOW</div>
</section>

<footer class="site-footer">
  <div class="brand" style="left:143px;top:3630px;font-size:34px">
    <span class="brand-mark" style="width:44px;height:44px"></span>Lumora
  </div>
  <span class="social" style="left:200px"></span>
  <span class="social" style="left:240px"></span>

  <div class="foot-col" style="left:405px">
    <h4>Quick Links</h4>
    <ul><li>Home</li><li>About</li><li>Our Services</li><li>Our Projects</li><li>Contact</li></ul>
  </div>
  <div class="foot-col" style="left:607px">
    <h4>Important</h4>
    <ul><li>Terms of Use</li><li>Site Map</li><li>Privacy Policy</li><li>Disclaimer</li></ul>
  </div>
  <div class="foot-col" style="left:809px;width:250px">
    <h4>Contact us</h4>
    <ul class="contact-list">
      <li><svg width="10" height="13" viewBox="0 0 10 13"><path d="M5 0a5 5 0 0 1 5 5c0 3-5 8-5 8S0 8 0 5a5 5 0 0 1 5-5z" fill="#d1321f"/><circle cx="5" cy="5" r="1.8" fill="#fff"/></svg><span style="font-size:12.5px;color:var(--muted)">Rm 908, 9/F, Kestrel Tower, 12 Lantern Road, Kwun Tong, Kowloon, Hong Kong</span></li>
      <li><svg width="10" height="13" viewBox="0 0 10 13"><rect x="1" y="0" width="8" height="13" rx="1.5" fill="#d1321f"/><rect x="2.5" y="2" width="5" height="7" fill="#fff"/></svg><span style="font-size:12.5px;color:var(--muted)">+852 2000 4810</span></li>
      <li><svg width="12" height="12" viewBox="0 0 12 12"><rect x="0" y="3" width="12" height="9" rx="1" fill="#d1321f"/><rect x="3" y="0" width="6" height="4" fill="#d1321f"/></svg><span style="font-size:12.5px;color:var(--muted)">+852 5000 7392</span></li>
      <li><svg width="12" height="10" viewBox="0 0 12 10"><rect width="12" height="10" rx="1" fill="#d1321f"/><path d="M0 1l6 5 6-5" stroke="#fff" fill="none"/></svg><span style="font-size:12.5px;color:var(--muted)">marketing@lumorasys.com.hk</span></li>
    </ul>
  </div>
  <div class="divider"></div>
  <div class="copyright">© 2023 by Lumora Systems &nbsp;|&nbsp; All Rights Reserved</div>
  <div class="chat"><svg width="18" height="16" viewBox="0 0 18 16"><path d="M9 1c4.4 0 8 2.7 8 6s-3.6 6-8 6l-4 2.5 1-3.2C3 11.3 1 9.3 1 7c0-3.3 3.6-6 8-6z" fill="#fff"/><circle cx="6" cy="7" r="1" fill="#d1321f"/><circle cx="9" cy="7" r="1" fill="#d1321f"/><circle cx="12" cy="7" r="1" fill="#d1321f"/></svg></div>
</footer>

</body>
</html>
```